Essential Oil 15ml - package of 6

Design of a box of 6 different essential oils.
+ design of the bottle stickers
My bottles are 15ml clear blue glass.

The pictures attached are my competitors...

Target Market(s)

TERVIK USA

Font styles to use
Serif

Requirements
Must have
• Our logo + "essential oil" and type (lavender, eucalyptus etc....)
• 15ml - 0.50 fl.oz.
• special color for the oil type.

```html
<!DOCTYPE html>
<html lang="en">
<head>
<meta charset="utf-8">
<title>Sela Vale Essential Oil Labels</title>
<link rel="stylesheet" href="https://fonts.googleapis.com/css2?family=Cormorant+Garamond:wght@500&family=Open+Sans:wght@400&family=Source+Sans+3:wght@700&display=swap">
<style>
  :root {
    --page: #ffffff;
    --label: #000000;
    --ink: #ffffff;
    --eucalyptus: #25634a;
    --orange: #e3711f;
    --rosemary: #6c1c25;
    --tea-tree: #4d522b;
    --lavender: #4b3b47;
    --peppermint: #2e4c32;
  }
  * { margin: 0; padding: 0; box-sizing: border-box; }
  html, body {
    width: 1200px;
    height: 635px;
    overflow: hidden;
    background: var(--page);
  }
  .sheet {
    position: relative;
    width: 1200px;
    height: 635px;
  }
  .label {
    position: absolute;
    width: 583px;
    height: 192px;
    background: var(--label);
    color: var(--ink);
    display: flex;
    flex-direction: column;
    align-items: center;
  }
  .col-left { left: 11px; }
  .col-right { left: 604px; }
  .row-1 { top: 19px; }
  .row-2 { top: 228px; }
  .row-3 { top: 428px; }

  .brand-mark {
    margin-top: 11px;
    width: 40px;
    height: 40px;
    border-radius: 50%;
    background: var(--ink);
  }
  .brand-name {
    margin-top: 6px;
    font-family: "Source Sans 3", sans-serif;
    font-weight: 700;
    font-size: 27px;
    line-height: 30px;
  }
  .category {
    margin-top: 9px;
    height: 28px;
    padding: 0 8px;
    border: 1px solid var(--accent);
    color: var(--accent);
    font-family: "Cormorant Garamond", serif;
    font-weight: 500;
    font-size: 21px;
    line-height: 27px;
    letter-spacing: 0.3px;
  }
  .oil-name {
    margin-top: 10px;
    font-family: "Cormorant Garamond", serif;
    font-weight: 500;
    font-size: 20px;
    line-height: 22px;
    letter-spacing: 0.6px;
  }
  .volume {
    margin-top: 6px;
    font-family: "Open Sans", sans-serif;
    font-size: 12px;
    line-height: 16px;
  }
  .eucalyptus { --accent: var(--eucalyptus); }
  .sweet-orange { --accent: var(--orange); }
  .rosemary { --accent: var(--rosemary); }
  .tea-tree { --accent: var(--tea-tree); }
  .lavender { --accent: var(--lavender); }
  .peppermint { --accent: var(--peppermint); }
</style>
</head>
<body>
<main class="sheet">
  <section class="label eucalyptus col-left row-1">
    <span class="brand-mark"></span>
    <p class="brand-name">Sela Vale</p>
    <p class="category">ESSENTIAL OIL</p>
    <p class="oil-name">EUCALYPTUS</p>
    <p class="volume">15ml (0.50 fl.oz)</p>
  </section>
  <section class="label sweet-orange col-right row-1">
    <span class="brand-mark"></span>
    <p class="brand-name">Sela Vale</p>
    <p class="category">ESSENTIAL OIL</p>
    <p class="oil-name">SWEET ORANGE</p>
    <p class="volume">15ml (0.50 fl.oz)</p>
  </section>
  <section class="label rosemary col-left row-2">
    <span class="brand-mark"></span>
    <p class="brand-name">Sela Vale</p>
    <p class="category">ESSENTIAL OIL</p>
    <p class="oil-name">ROSEMARY</p>
    <p class="volume">15ml (0.50 fl.oz)</p>
  </section>
  <section class="label tea-tree col-right row-2">
    <span class="brand-mark"></span>
    <p class="brand-name">Sela Vale</p>
    <p class="category">ESSENTIAL OIL</p>
    <p class="oil-name">TEA TREE</p>
    <p class="volume">15ml (0.50 fl.oz)</p>
  </section>
  <section class="label lavender col-left row-3">
    <span class="brand-mark"></span>
    <p class="brand-name">Sela Vale</p>
    <p class="category">ESSENTIAL OIL</p>
    <p class="oil-name">LAVENDER</p>
    <p class="volume">15ml (0.50 fl.oz)</p>
  </section>
  <section class="label peppermint col-right row-3">
    <span class="brand-mark"></span>
    <p class="brand-name">Sela Vale</p>
    <p class="category">ESSENTIAL OIL</p>
    <p class="oil-name">PEPPERMINT</p>
    <p class="volume">15ml (0.50 fl.oz)</p>
  </section>
</main>
</body>
</html>
```